Logo, Web and Mobile Designs for enterprise social media platform

All the details are in the attached document, please start reading the scope document first which explains what is this project about and the details about the needed deliverables, after that please read the UI_Requirements document which will detail what is expected regarding the coded web version since this is a coded contest, it is very important that you meet the UI requirements or suggest something else but we will need to agree first before working on the coded version

Good Luck

Target Market(s)

Enterprise Social Media

Industry/Entity Type

Media

Coding

Coded - Design and coding required

Number of Pages Required

5+ page

Font styles to use
Sans Serif

Requirements
Must have
• All the must haves are listed in the scope document so please check before you start

```html
<!DOCTYPE html>
<html lang="en">
<head>
<meta charset="utf-8">
<title>Teamora — Login</title>
<link rel="stylesheet" href="https://fonts.googleapis.com/css2?family=Lato:wght@400;700;900&display=swap">
<style>
:root{
  --bar:#1b1d2a;
  --panel:#1c1f2b;
  --panel-head:#2b2f3d;
  --field:#2e3241;
  --field-text:#7f8596;
  --accent:#1fc3f7;
  --accent-green:#25c4a0;
  --muted:#8b909c;
  --white:#ffffff;
  --footer:#050505;
  --hero-light:#8a7564;
  --hero-dark:#5e4a3b;
}
*{box-sizing:border-box;margin:0;padding:0}
html,body{width:1200px;height:789px;overflow:hidden}
body{font-family:"Lato",sans-serif;background:var(--footer);position:relative}
.site-header{position:absolute;left:0;top:0;width:1200px;height:90px;background:var(--bar)}
.brand{position:absolute;left:103px;top:27px;font-size:29px;font-weight:400;color:var(--white);line-height:36px}
.nav-btn{position:absolute;top:28px;height:32px;line-height:32px;text-align:center;color:var(--white);font-size:15px;border-radius:2px;text-decoration:none}
.nav-login{left:899px;width:100px;background:var(--accent)}
.nav-register{left:1003px;width:98px;background:#2e3242}
.hero{position:absolute;left:0;top:90px;width:1200px;height:630px;
  background:linear-gradient(135deg,var(--hero-light) 0%,var(--hero-dark) 100%)}
.login-card{position:absolute;left:427px;top:202px;width:379px;height:419px;background:var(--panel);border-radius:2px}
.card-title{height:61px;background:var(--panel-head);color:var(--white);font-weight:900;font-size:19px;letter-spacing:2px;text-align:center;line-height:61px;border-bottom:1px solid #3a3e4c}
.field{position:absolute;left:28px;width:323px;height:51px;background:var(--field);border-radius:2px;color:var(--field-text);font-size:16px;line-height:51px;padding-left:24px}
.btn-submit{position:absolute;left:28px;top:293px;width:323px;height:51px;background:var(--accent);color:var(--white);font-weight:900;font-size:16px;text-align:center;line-height:51px;border-radius:2px}
.card-link{position:absolute;top:363px;font-size:14px}
.link-forgot{left:28px;color:var(--muted)}
.link-register{right:28px;color:var(--accent-green)}
.slider-dots{position:absolute;top:696px;left:577px;display:flex;gap:9px}
.dot{width:9px;height:9px;border-radius:50%;background:var(--white)}
.dot.active{background:var(--accent)}
.site-footer{position:absolute;left:0;top:720px;width:1200px;height:69px;background:var(--footer);text-align:center;line-height:69px;color:#a5a8b0;font-size:12px}
.site-footer .sep{color:#555;margin:0 7px}
</style>
</head>
<body>
<header class="site-header">
  <div class="brand">Teamora</div>
  <a class="nav-btn nav-login">LOGIN</a>
  <a class="nav-btn nav-register">REGISTER</a>
</header>
<section class="hero" role="img" aria-label="Background photo: blurred desk with notebook, phone, pen and coffee cup"></section>
<form class="login-card">
  <h1 class="card-title">LOGIN TO YOUR ACCOUNT</h1>
  <div class="field" style="top:95px">Teamora ID</div>
  <div class="field" style="top:157px">Email</div>
  <div class="field" style="top:218px">Password</div>
  <div class="btn-submit">LOGIN NOW</div>
  <span class="card-link link-forgot">Forgot Username?</span>
  <span class="card-link link-register">Register New Account?</span>
</form>
<div class="slider-dots"><span class="dot active"></span><span class="dot"></span><span class="dot"></span></div>
<footer class="site-footer">Copyright 2015 yoursite<span class="sep">|</span>All Rights Reserved</footer>
</body>
</html>
```